The Lantern and the Orchard: Notes From Quiet Mornings

We need a book cover/spine and back cover for a multi author book called the Lantern and The Orchard: Notes from Quiet Mornings. This will be a collection of stories from women who major transformational stories to tell. They embark on a voyage, find themselves in uncharted territory, find friends or allies and in the end find themselves back home to themselves. I want this book cover to feel fun of wonder, adventure, intrigue with a a dainty energy. I have uploaded some images for inspiration but not to use in the design because they are not images I have permission to use.

```html
<!DOCTYPE html>
<html lang="en">
<head>
<meta charset="utf-8">
<title>The Lantern and the Orchard: Notes From Quiet Mornings</title>
<link rel="stylesheet" href="https://fonts.googleapis.com/css2?family=Kaushan+Script&family=Archivo+Narrow:wght@700&family=Arimo:wght@700&display=swap">
<style>
  :root {
    --sky-top: #9fdcf1;
    --sky-mid: #c4ebf7;
    --haze: #eef8fb;
    --field-light: #f0b835;
    --field-deep: #dc9a1e;
    --field-shadow: #c7891c;
    --title-ink: #1d4a5e;
    --subtitle-grey: #737c82;
    --and-grey: #4f5a61;
    --author-white: #ffffff;
  }
  html, body {
    margin: 0;
    padding: 0;
    width: 909px;
    height: 1200px;
    overflow: hidden;
    background: #ffffff;
  }
  .cover {
    position: relative;
    width: 909px;
    height: 1200px;
    overflow: hidden;
  }
  .cover-photo {
    position: absolute;
    inset: 0;
    background:
      linear-gradient(180deg,
        var(--sky-top) 0%,
        var(--sky-mid) 30%,
        var(--haze) 49%,
        var(--field-light) 51%,
        var(--field-deep) 75%,
        var(--field-shadow) 100%);
  }
  .title-art {
    position: absolute;
    left: 0;
    top: 0;
    width: 909px;
    height: 520px;
  }
  .title-script {
    font-family: "Kaushan Script", cursive;
    fill: var(--title-ink);
  }
  .title-and {
    font-family: "Arimo", Arial, sans-serif;
    font-weight: 700;
    fill: var(--and-grey);
  }
  .subtitle {
    position: absolute;
    left: 231px;
    top: 526px;
    width: 556px;
    margin: 0;
    font-family: "Archivo Narrow", "Arial Narrow", sans-serif;
    font-weight: 700;
    font-size: 48px;
    line-height: 48px;
    letter-spacing: 0.5px;
    color: var(--subtitle-grey);
    text-align: center;
    white-space: nowrap;
  }
  .authors {
    position: absolute;
    left: 407px;
    top: 922px;
    margin: 0;
    padding: 0;
    list-style: none;
  }
  .authors li {
    font-family: "Arimo", Arial, sans-serif;
    font-weight: 700;
    font-size: 24px;
    line-height: 54.5px;
    color: var(--author-white);
    white-space: nowrap;
  }
</style>
</head>
<body>
  <main class="cover">
    <div class="cover-photo" role="img" aria-label="Photograph of a woman with long dark hair seen from behind, walking through a field of yellow wildflowers under a pale blue sky"></div>

    <svg class="title-art" viewBox="0 0 909 520" xmlns="http://www.w3.org/2000/svg">
      <text class="title-script" x="192" y="285" font-size="150" textLength="630" lengthAdjust="spacingAndGlyphs">The Lantern</text>
      <text class="title-and" x="146" y="340" font-size="40" textLength="116" lengthAdjust="spacingAndGlyphs">AND</text>
      <text class="title-script" x="192" y="465" font-size="150" textLength="636" lengthAdjust="spacingAndGlyphs">the Orchard</text>
    </svg>

    <p class="subtitle">NOTES FROM QUIET MORNINGS</p>

    <ul class="authors">
      <li>AUTHER NO. 1</li>
      <li>AUTHER NO. 2</li>
      <li>AUTHER NO. 3</li>
      <li>AUTHER NO. 4</li>
    </ul>
  </main>
</body>
</html>
```